Pelican HVAC WordPress website design

Design a new modern, clean, website for HVAC mechanical business that uses company logo/colors for branding and recognition. Files attached are just for band and color information. Here is a website design that appeals to me https://www.corvellsupply.example/

A clear description of who we are and what we do

An easily-navigated site map

An easily-navigated site map for mobile devices

Easy-to-find contact information

Obvious call to action for service, installs or to schedule estimates

about us page

Provide a way for potential customers to contact us via text or email

provide a way that allows a customer to upload a picture to request a service call or quote.
Updates

I'm looking for the design to be completed in WordPress

Industry/Entity Type

HVAC Mechanical & Building Automation / Controls contractor

Coding

Coded - Design and coding required

Number of Pages Required

5+ page

Colors
0054AA
0677BA
7BADD7
CADEEF
E8F1F8

Requirements
Must have
• Design a new modern, clean, website for HVAC mechanical business that uses company logo/colors for branding and recognition. Files attached are just for band and color information. Here is a website design that appeals to me https://www.corvellsupply.example/ A clear description of who we are and what we do An easily-navigated site map An easily-navigated site map for mobile devices Easy-to-find contact information Obvious call to action for service, installs or to schedule estimates about us page Provide a way for potential customers to contact us via text or email provide a way that allows a customer to upload a picture to request a service call or quote.
Nice to have

```html
<!DOCTYPE html>
<html lang="en">
<head>
<meta charset="utf-8">
<title>Pelican HVAC — Home</title>
<link href="https://fonts.googleapis.com/css2?family=Roboto+Slab:wght@400;500;700;800&family=Roboto:wght@400;500;700&display=swap" rel="stylesheet">
<style>
:root{
  --navy:#0b3263;
  --navy-deep:#072a55;
  --ink:#1d3656;
  --grey-band:#c4c9cf;
  --grey-text:#6b6f74;
  --white:#ffffff;
  --black:#0b0b0b;
  --light:#e8f1f8;
}
*{box-sizing:border-box;margin:0;padding:0}
html,body{width:1200px;height:3146px;overflow:hidden;background:var(--white)}
body{position:relative;font-family:"Roboto Slab",serif;color:var(--ink)}
.abs{position:absolute}
a{color:inherit;text-decoration:none}

/* header */
.site-header{left:0;top:0;width:1200px;height:118px;background:var(--white);border-top:4px solid #b9bdc2;z-index:5}
.brand{left:146px;top:18px;display:flex;align-items:center;gap:10px;font:700 30px "Roboto Slab",serif;color:var(--navy);white-space:nowrap}
.brand-dot{width:56px;height:56px;border-radius:50%;background:var(--navy);flex:none}
.btn-outline{display:flex;align-items:center;justify-content:center;border:2px solid var(--navy);border-radius:30px;font:500 13px "Roboto Slab",serif;color:var(--navy);background:var(--white);text-transform:uppercase;white-space:nowrap}
.header-cta{left:503px;top:14px;width:238px;height:42px}
.call-badge{left:747px;top:-4px;width:297px;height:70px;background:var(--navy);border-radius:0 0 150px 150px/0 0 55px 55px;border:3px solid #aab1b9;border-top:none;display:flex;align-items:center;gap:14px;padding-left:52px;color:var(--white)}
.call-icon{width:30px;height:30px;border-radius:50%;background:var(--white);display:flex;align-items:center;justify-content:center;flex:none}
.call-label{font:500 11px "Roboto Slab",serif;display:block;white-space:nowrap}
.call-number{font:700 21px Roboto,sans-serif;display:block;margin-top:1px}
.main-nav{left:450px;top:82px;display:flex;font:500 14px "Roboto Slab",serif;color:var(--ink);text-transform:uppercase;white-space:nowrap}
.main-nav a{padding:6px 23px}
.main-nav .current{border:2px solid #bfc4ca;border-radius:20px;padding:4px 8px;margin-right:14px}
.nav-search{left:1040px;top:88px}

/* hero */
.hero{left:0;top:118px;width:1200px;height:640px}
.hero-title{left:144px;top:222px;font:800 69px/70px "Roboto Slab",serif;color:var(--white);text-transform:uppercase;text-shadow:0 3px 6px rgba(0,0,0,.5)}
.hero-cta{left:144px;top:461px;width:237px;height:41px}
.hero-dots{left:575px;top:632px;display:flex;gap:8px;align-items:center}
.hero-dots span{width:10px;height:10px;border-radius:50%;background:var(--white)}
.hero-dots .on{width:15px;height:15px;background:transparent;border:2px solid var(--white)}

/* about */
.about-backdrop{left:0;top:700px;width:1200px;height:680px;background:linear-gradient(90deg,#eef0f4 0%,#fbfbfd 45%,#f4f6f9 100%);z-index:-1}
.about-photos{left:112px;top:812px;width:456px;height:427px}
.about-title{left:602px;top:826px;font:700 41px "Roboto Slab",serif;color:var(--ink);white-space:nowrap}
.about-copy{left:602px;top:892px;width:453px;font:400 13.5px/23.3px "Roboto Slab",serif;color:var(--grey-text);text-align:justify}
.about-more{left:600px;top:1158px;width:135px;height:44px}
.side-word{font:800 62px "Roboto Slab",serif;color:#dcdee2;writing-mode:vertical-rl;transform:rotate(180deg);letter-spacing:1px}
.about-word{left:1108px;top:766px}
.van{left:792px;top:1180px;width:395px;height:155px;border-radius:44px 60px 20px 20px;background:linear-gradient(180deg,#e4e7ea 0%,#cdd2d8 100%);z-index:3}

/* services */
.services{left:0;top:1276px;width:1200px;height:668px}
.services-title{left:0;top:1378px;width:1200px;text-align:center;font:700 43px "Roboto Slab",serif;color:var(--white)}
.service{width:184px;height:184px;border-radius:50%;border:2px solid var(--white);display:flex;flex-direction:column;align-items:center;justify-content:flex-start;padding-top:34px;gap:14px;color:var(--white);font:700 14px "Roboto Slab",serif;top:1477px;white-space:nowrap}
.service-icon{height:64px;display:flex;align-items:flex-end;justify-content:center}
.service.active{background:rgba(255,255,255,.12)}
.service.active::after{content:"";position:absolute;bottom:-14px;left:50%;margin-left:-10px;border:10px solid transparent;border-top:12px solid var(--white);border-bottom:none}
.arrow{width:44px;height:44px;border-radius:50%;border:2px solid var(--white);top:1547px;display:flex;align-items:center;justify-content:center}
.services-copy{left:290px;top:1697px;width:620px;text-align:center;font:400 13.5px/24px "Roboto Slab",serif;color:var(--white)}
.services-more{left:533px;top:1792px;width:135px;height:43px;border-color:var(--white);background:transparent;color:var(--white)}

/* quote */
.quote-backdrop{left:0;top:1880px;width:1200px;height:760px;background:linear-gradient(180deg,#f7f8fa 0%,#e4e8ee 40%,#d7dde5 100%);z-index:-1}
.contact-word{left:58px;top:2042px}
.quote-title{left:0;top:2024px;width:1200px;text-align:center;font:700 41px "Roboto Slab",serif;color:var(--ink)}
.quote-sub{left:0;top:2088px;width:1200px;text-align:center;font:400 19px "Roboto Slab",serif;color:#3b4a5c}
.field{background:rgba(255,255,255,.9);border:2px solid #c3c8cf;border-radius:24px;padding:0 30px;display:flex;align-items:center;font:400 12.5px "Roboto Slab",serif;color:#6d7178}
.field.msg{align-items:flex-start;padding-top:16px;border-radius:26px}
.upload{left:214px;top:2407px;width:164px;height:46px;gap:8px}
.mail-q{left:413px;top:2418px;font:400 16px "Roboto Slab",serif;color:#2c3643;white-space:nowrap}
.radio{top:2421px;display:flex;align-items:center;gap:6px;font:500 12px "Roboto Slab",serif;color:#6c7076}
.radio i{width:15px;height:15px;border:2px solid #a4a9b0;border-radius:50%;display:block}
.submit{left:533px;top:2468px;width:134px;height:42px}

/* footer */
.footer-shape{left:0;top:2560px;width:1200px;height:586px}
.footer-brand{left:0;top:2680px;width:1200px;display:flex;justify-content:center;align-items:center;gap:10px;font:700 30px "Roboto Slab",serif;color:var(--white)}
.footer-brand .brand-dot{background:var(--white);width:48px;height:48px}
.f-head{top:2798px;font:500 18px Roboto,sans-serif;color:var(--white);text-transform:uppercase;white-space:nowrap}
.f-text{font:400 12.5px/21px Roboto,sans-serif;color:var(--white)}
.f-item{left:171px;display:flex;gap:20px;align-items:flex-start}
.f-item svg{flex:none;margin-top:3px}
.newsletter-input{left:508px;top:2915px;width:254px;height:45px;border:2px solid #555;border-radius:24px;padding-left:20px;display:flex;align-items:center;font:400 13px Roboto,sans-serif;color:var(--white)}
.subscribe{left:508px;top:2974px;width:254px;height:42px;border-radius:22px;background:var(--white);display:flex;align-items:center;justify-content:center;font:500 14px Roboto,sans-serif;color:var(--black)}
.quick{left:917px;top:2854px;list-style:none;font:400 12.5px/27.5px Roboto,sans-serif;color:var(--white)}
.f-rule{left:171px;top:3062px;width:860px;height:1px;background:#2a2a2a}
.copyright{left:171px;top:3098px;font:400 12.5px Roboto,sans-serif;color:var(--white);white-space:nowrap}
.social{top:3098px;width:16px;height:16px;border-radius:50%;border:2px solid var(--white)}
</style>
</head>
<body>

<header class="abs site-header">
  <a class="abs brand" href="#"><span class="brand-dot"></span>Pelican HVAC</a>
  <a class="abs btn-outline header-cta" href="#">Schedule an appointment</a>
  <a class="abs call-badge" href="#">
    <span class="call-icon"><svg width="16" height="16" viewBox="0 0 24 24"><path fill="#0b3263" d="M6.6 10.8a15.1 15.1 0 0 0 6.6 6.6l2.2-2.2a1 1 0 0 1 1-.25 11.4 11.4 0 0 0 3.6.57 1 1 0 0 1 1 1V20a1 1 0 0 1-1 1A17 17 0 0 1 3 4a1 1 0 0 1 1-1h3.5a1 1 0 0 1 1 1c0 1.25.2 2.45.57 3.57a1 1 0 0 1-.25 1z"/></svg></span>
    <span><span class="call-label">REQUEST A SERVICE CALL</span><span class="call-number">555-014-2287</span></span>
  </a>
  <nav class="abs main-nav">
    <a class="current" href="#">Home</a><a href="#">Who We Are</a><a href="#">What We Do</a><a href="#">News</a><a href="#">Contact Us</a>
  </nav>
  <svg class="abs nav-search" width="14" height="14" viewBox="0 0 24 24"><circle cx="10" cy="10" r="7" fill="none" stroke="#1d3656" stroke-width="3"/><path d="M15 15l7 7" stroke="#1d3656" stroke-width="3"/></svg>
</header>

<section class="abs hero">
  <svg width="1200" height="640" viewBox="0 118 1200 640">
    <defs>
      <linearGradient id="sky" x1="0" y1="0" x2="0" y2="1">
        <stop offset="0" stop-color="#2a3f66"/><stop offset=".35" stop-color="#c98a55"/><stop offset=".55" stop-color="#6a5a55"/><stop offset=".75" stop-color="#1d3252"/><stop offset="1" stop-color="#122440"/>
      </linearGradient>
    </defs>
    <path d="M0 118H1200V520Q600 982 0 520Z" fill="#a9abae"/>
    <path role="img" aria-label="Evening city skyline over the water" d="M0 118H1200V518Q600 942 0 518Z" fill="url(#sky)"/>
  </svg>
</section>
<h1 class="abs hero-title">HVAC<br>Mechanical<br>Business</h1>
<a class="abs btn-outline hero-cta" href="#">Schedule an appointment</a>
<div class="abs hero-dots"><span></span><span class="on"></span><span></span></div>

<div class="abs about-backdrop" role="img" aria-label="Faded outdoor air conditioning units"></div>
<div class="abs side-word about-word">ABOUT</div>
<svg class="abs about-photos" width="456" height="427" viewBox="0 0 456 427" role="img" aria-label="Technician servicing rooftop units and a close view of an outdoor condenser">
  <defs>
    <linearGradient id="p1" x1="0" y1="0" x2="1" y2="1"><stop offset="0" stop-color="#7d8a9a"/><stop offset=".6" stop-color="#c29a6c"/><stop offset="1" stop-color="#3b3f48"/></linearGradient>
    <linearGradient id="p2" x1="0" y1="0" x2="0" y2="1"><stop offset="0" stop-color="#b7c2cc"/><stop offset="1" stop-color="#d7a874"/></linearGradient>
    <linearGradient id="p3" x1="0" y1="0" x2="1" y2="0"><stop offset="0" stop-color="#c9a57a"/><stop offset="1" stop-color="#6f8a72"/></linearGradient>
  </defs>
  <ellipse cx="228" cy="200" rx="227" ry="157" fill="url(#p1)"/>
  <ellipse cx="146" cy="100" rx="146" ry="100" fill="#fff"/>
  <ellipse cx="148" cy="100" rx="130" ry="83" fill="url(#p2)"/>
  <ellipse cx="286" cy="322" rx="155" ry="105" fill="#fff"/>
  <ellipse cx="288" cy="322" rx="136" ry="88" fill="url(#p3)"/>
</svg>
<h2 class="abs about-title">Who We Are</h2>
<p class="abs about-copy">Sed ut perspiciatis unde omnis iste natus error sit voluptatem accusantium doloremque laudantium, totam rem aperiam, eaque ipsa quae ab illo inventore veritatis et quasi architecto beatae vitae dicta sunt explicabo. Nemo enim ipsam voluptatem quia voluptas sit aspernatur aut odit aut fugit, sed quia consequuntur magni dolores eos qui ratione voluptatem sequi nesciunt. Neque porro quisquam est, qui dolorem ipsum quia dolorSed ut perspiciatis unde omnis iste natus error sit voluptatem accusantium doloremque laudantium, totam rem aperiam, eaque ipsa quae ab illo inventore veritatis et quasi architecto beatae vitae dicta sunt explicabo. Nemo enim ipsam voluptatem quia voluptas</p>
<a class="abs btn-outline about-more" href="#">Read more</a>
<div class="abs van" role="img" aria-label="Company service van"></div>

<svg class="abs services" width="1200" height="668" viewBox="0 0 1200 668">
  <ellipse cx="600" cy="334" rx="620" ry="334" fill="var(--grey-band)"/>
  <ellipse cx="600" cy="340" rx="575" ry="318" fill="var(--navy-deep)" role="img" aria-label="Dark blue backdrop with faint condenser units"/>
</svg>
<h2 class="abs services-title">What We Do</h2>
<a class="abs arrow" style="left:112px" href="#"><svg width="14" height="14" viewBox="0 0 24 24"><path d="M15 4l-8 8 8 8" fill="none" stroke="#fff" stroke-width="3"/></svg></a>
<a class="abs arrow" style="left:1043px" href="#"><svg width="14" height="14" viewBox="0 0 24 24"><path d="M9 4l8 8-8 8" fill="none" stroke="#fff" stroke-width="3"/></svg></a>
<div class="abs service" style="left:202px">
  <span class="service-icon"><svg width="70" height="56" viewBox="0 0 70 56" fill="none" stroke="#fff" stroke-width="2.5"><rect x="2" y="2" width="66" height="22" rx="3"/><path d="M8 16h54"/><path d="M18 30v22M8 41h20M11 34l14 14M25 34L11 48"/><path d="M40 32q4 5 0 10t0 10M50 32q4 5 0 10t0 10M60 32q4 5 0 10t0 10"/></svg></span>
  Air Conditioning</div>
<div class="abs service active" style="left:406px">
  <span class="service-icon"><svg width="60" height="60" viewBox="0 0 60 60" fill="none" stroke="#fff" stroke-width="2.5"><circle cx="16" cy="22" r="8"/><path d="M16 6v5M16 33v5M2 22h5M25 22h5M6 12l3 3M26 12l-3 3M6 32l3-3"/><rect x="36" y="4" width="12" height="38" rx="6"/><circle cx="42" cy="48" r="9"/><path d="M42 14v30M52 10h6M52 18h6M52 26h6"/></svg></span>
  Heating</div>
<div class="abs service" style="left:610px">
  <span class="service-icon"><svg width="62" height="62" viewBox="0 0 62 62" fill="none" stroke="#fff" stroke-width="2.5"><circle cx="31" cy="31" r="19"/><path d="M31 4v7M31 51v7M4 31h7M51 31h7M12 12l5 5M45 45l5 5M12 50l5-5M45 17l5-5"/><path d="M24 38l9-9a6 6 0 1 0-3-3l-9 9z"/></svg></span>
  Maintenance</div>
<div class="abs service" style="left:814px">
  <span class="service-icon"><svg width="64" height="62" viewBox="0 0 64 62" fill="none" stroke="#fff" stroke-width="2.5"><circle cx="38" cy="18" r="16"/><path d="M31 26l14-16"/><circle cx="32" cy="13" r="3"/><circle cx="44" cy="23" r="3"/><path d="M2 44h10v16H2zM12 46h14l10 4h14l10-6v4l-14 10H12"/></svg></span>
  Special Offers</div>
<p class="abs services-copy">Sed ut perspiciatis unde omnis iste natus error sit voluptatem accusantium doloremque laudantium, totam rem aperiam, eaque ipsa quae ab illo inventore veritatis et quasi architecto beatae vitae dicta sunt explicabo. Nemo enim ipsam voluptatem quia voluptas sit aspernatur au</p>
<a class="abs btn-outline services-more" href="#">Read more</a>

<div class="abs quote-backdrop" role="img" aria-label="Faded technician installing an indoor air conditioner"></div>
<div class="abs side-word contact-word">CONTACT</div>
<h2 class="abs quote-title">Request A Quote</h2>
<p class="abs quote-sub">Contact us via text or email</p>
<form>
  <div class="abs field" style="left:214px;top:2170px;width:381px;height:46px">Enter Name *</div>
  <div class="abs field" style="left:606px;top:2170px;width:381px;height:46px">Enter Email *</div>
  <div class="abs field" style="left:214px;top:2234px;width:381px;height:46px">Enter Phone *</div>
  <div class="abs field" style="left:606px;top:2234px;width:381px;height:46px">Address</div>
  <div class="abs field msg" style="left:214px;top:2298px;width:773px;height:93px">Message</div>
  <a class="abs btn-outline upload" href="#">Upload picture
    <svg width="20" height="20" viewBox="0 0 24 24" fill="none" stroke="#0b3263" stroke-width="2.5"><path d="M12 16V3M6 9l6-6 6 6M3 15v6h18v-6"/></svg></a>
  <span class="abs mail-q">Join Our Mailing List</span>
  <span class="abs radio" style="left:602px"><i></i>YES</span>
  <span class="abs radio" style="left:674px"><i></i>NO</span>
  <a class="abs btn-outline submit" href="#">Submit</a>
</form>

<svg class="abs footer-shape" width="1200" height="586" viewBox="0 2560 1200 586">
  <path d="M0 2790Q600 2330 1200 2790V3146H0Z" fill="#9a9ea3"/>
  <path d="M0 2810Q600 2356 1200 2810V3146H0Z" fill="var(--black)"/>
</svg>
<div class="abs footer-brand"><span class="brand-dot"></span>Pelican HVAC</div>

<h3 class="abs f-head" style="left:171px">Contact Us</h3>
<div class="abs f-item f-text" style="top:2852px">
  <svg width="16" height="20" viewBox="0 0 16 20"><path d="M8 0a7 7 0 0 0-7 7c0 5 7 13 7 13s7-8 7-13a7 7 0 0 0-7-7zm0 10a3 3 0 1 1 0-6 3 3 0 0 1 0 6z" fill="#fff"/></svg>
  <span>123,ores eos qui ratione<br>voluptatem sequi nesciun</span></div>
<div class="abs f-item f-text" style="top:2910px">
  <svg width="16" height="16" viewBox="0 0 24 24"><path fill="#fff" d="M6.6 10.8a15.1 15.1 0 0 0 6.6 6.6l2.2-2.2a1 1 0 0 1 1-.25 11.4 11.4 0 0 0 3.6.57 1 1 0 0 1 1 1V20a1 1 0 0 1-1 1A17 17 0 0 1 3 4a1 1 0 0 1 1-1h3.5a1 1 0 0 1 1 1c0 1.25.2 2.45.57 3.57a1 1 0 0 1-.25 1z"/></svg>
  <span>Phone:<br>555-014-2287</span></div>
<div class="abs f-item f-text" style="top:2962px">
  <svg width="17" height="13" viewBox="0 0 17 13"><path d="M0 0h17v13H0z" fill="#fff"/><path d="M0 0l8.5 7L17 0" fill="none" stroke="#000" stroke-width="1.5"/></svg>
  <span>Email:<br>info@pelicanhvac.example</span></div>

<h3 class="abs f-head" style="left:508px">Sign Up For Newsletter</h3>
<p class="abs f-text" style="left:508px;top:2856px;width:290px">excepteur sint occaecat cupidatat non proident, sunt in culpa</p>
<div class="abs newsletter-input">Enter email</div>
<a class="abs subscribe" href="#">SUBSCRIBE</a>

<h3 class="abs f-head" style="left:913px">Quick Links</h3>
<ul class="abs quick">
  <li>Home</li><li>Our Services</li><li>About Us</li><li>Why Use Broker</li><li>Blog</li><li>Contact Us</li>
</ul>

<div class="abs f-rule"></div>
<p class="abs copyright">Copyright ©2024 Pelican HVAC | Accessibility Statement | Privacy Policy | Sitemap</p>
<a class="abs social" style="left:935px" href="#" aria-label="Social profile"></a>
<a class="abs social" style="left:973px" href="#" aria-label="Social profile"></a>
<a class="abs social" style="left:1011px" href="#" aria-label="Social profile"></a>

</body>
</html>
```